Business Cards for a law firm

Business cards for our law firm. Use our silhoette logo and OAK PARTNERS - check our website (www.oakpartners.example)

Contact Information for Business Card

our silhouette logo, OAK PARTNERS, 800-555-0147, Dorian Pemberton, dorian@oakpartners.example

Requirements
Must have
• our silhouette logo, OAK PARTNERS, 800-555-0147, Dorian Pemberton, dorian@oakpartners.example

```html
<!DOCTYPE html>
<html lang="en">
<head>
<meta charset="utf-8">
<title>Oak Partners — Business Cards</title>
<link rel="stylesheet" href="https://fonts.googleapis.com/css2?family=Montserrat:wght@500;600&family=Open+Sans:wght@400;700&display=swap">
<style>
  :root {
    --navy: #25326b;
    --white: #ffffff;
    --backdrop: #1c1c1d;
    --mark-tint: #dfe2ee;
  }
  * { margin: 0; padding: 0; box-sizing: border-box; }
  html, body { width: 1200px; height: 801px; overflow: hidden; }
  body {
    background: var(--backdrop);
    display: flex;
    align-items: center;
    justify-content: center;
    gap: 44px;
    font-family: "Open Sans", sans-serif;
  }
  .card {
    width: 540px;
    height: 309px;
    border-radius: 20px;
    overflow: hidden;
    background: var(--navy);
    color: var(--white);
    position: relative;
  }

  /* Front */
  .card-front { display: flex; }
  .mark-panel {
    width: 214px;
    background: var(--white);
    display: flex;
    align-items: center;
    justify-content: center;
  }
  .mark-area {
    width: 150px;
    height: 220px;
    background: linear-gradient(180deg, var(--mark-tint), #c9cee3);
    border-radius: 6px;
  }
  .details {
    flex: 1;
    padding: 30px 0 0 34px;
  }
  .firm-name {
    font-family: "Montserrat", sans-serif;
    font-weight: 500;
    font-size: 21px;
    letter-spacing: 3.5px;
  }
  .person-name {
    margin-top: 28px;
    font-weight: 700;
    font-size: 20px;
    line-height: 1.1;
  }
  .role { font-size: 11px; margin-top: 2px; }
  .address {
    margin-top: 12px;
    font-size: 11px;
    line-height: 1.35;
    font-style: normal;
  }
  .contact-list {
    list-style: none;
    margin-top: 10px;
    font-size: 11px;
    line-height: 1.7;
  }
  .contact-list li { display: flex; align-items: center; gap: 7px; }
  .contact-list svg { width: 10px; height: 10px; fill: var(--white); flex: none; }

  /* Back */
  .card-back {
    display: flex;
    align-items: center;
    justify-content: center;
  }
  .back-name {
    font-family: "Montserrat", sans-serif;
    font-weight: 500;
    font-size: 36px;
    letter-spacing: 6px;
  }
</style>
</head>
<body>
  <section class="card card-front">
    <div class="mark-panel">
      <div class="mark-area" role="img" aria-label="Area for the firm's brand mark"></div>
    </div>
    <div class="details">
      <h1 class="firm-name">OAK PARTNERS</h1>
      <p class="person-name">Dorian Pemberton</p>
      <p class="role">Lawyer</p>
      <address class="address">415 Cedar Grove Ave. #112<br>Millbrook, OH 43000</address>
      <ul class="contact-list">
        <li>
          <svg viewBox="0 0 10 10" aria-hidden="true"><path d="M2 0.5 L3.6 2.6 L2.6 3.6 Q3.6 5.9 6.4 7.4 L7.4 6.4 L9.5 8 L8.3 9.5 Q2.8 8.8 0.5 1.7 Z"/></svg>
          800-555-0147
        </li>
        <li>
          <svg viewBox="0 0 10 10" aria-hidden="true"><path d="M0.5 2 H9.5 V8.5 H0.5 Z M1 2.4 L5 5.6 L9 2.4" stroke="#25326b" stroke-width="0.8"/></svg>
          dorian@oakpartners.example
        </li>
        <li>
          <svg viewBox="0 0 10 10" aria-hidden="true"><circle cx="5" cy="5" r="4.6"/><path d="M0.6 5 H9.4 M5 0.5 V9.5 M5 0.5 Q2.2 5 5 9.5 M5 0.5 Q7.8 5 5 9.5" stroke="#25326b" stroke-width="0.7" fill="none"/></svg>
          www.oakpartners.example
        </li>
      </ul>
    </div>
  </section>

  <section class="card card-back">
    <p class="back-name">OAK PARTNERS</p>
  </section>
</body>
</html>
```